Quiet Harbor Prints gallery website

I need a Website for a gallery with a shopify integration or maybe even better also compatible with squarespace.
the website should have following riders: Künstler, Veranstaltungen, Shop, About Us.
some nice examples for inspiration of the website architecture are:
https://www.lindwerkraum.com/
https://www.plattenbau-salon.com/de/
https://moorlichtraum.de/
It should be easy for us to make adaptations and fill the website with new content.
Attached there is the CI an logo for the brand.
Target Market(s)
Art Collectors,
Industry/Entity Type
artgallery
Coding
Coded - Design and coding required
Number of Pages Required
3 page
Font styles to use
Look and feel

```html
<!DOCTYPE html>
<html lang="en">
<head>
<meta charset="utf-8">
<title>Quiet Harbor Prints</title>
<link href="https://fonts.googleapis.com/css2?family=Josefin+Sans:wght@300;400;600;700&display=swap" rel="stylesheet">
<style>
:root{
  --red:#c0111f;
  --ink:#111111;
  --white:#ffffff;
  --muted:#333333;
  --dark:#1b1512;
}
*{margin:0;padding:0;box-sizing:border-box}
html,body{width:1200px;height:2948px;overflow:hidden;background:var(--white)}
body{position:relative;font-family:"Josefin Sans",sans-serif;color:var(--ink)}
.abs{position:absolute}

/* header */
.site-header{position:absolute;left:0;top:0;width:1200px;height:126px;background:var(--white)}
.brand{position:absolute;display:flex;align-items:center;gap:10px;font-weight:300;color:var(--ink);white-space:nowrap}
.brand-mark{width:12px;height:12px;border:2px solid var(--red)}
.brand--header{left:111px;top:48px;font-size:19px;letter-spacing:.5px}
.main-nav{position:absolute;top:52px;left:499px;display:flex;gap:41px;font-size:18px;font-weight:300}
.main-nav a{color:var(--ink);text-decoration:none}
.btn{display:flex;align-items:center;justify-content:center;background:var(--red);color:var(--white);font-weight:600;text-decoration:none;box-shadow:4px 4px 0 #2a0a0a}
.btn--login{position:absolute;left:950px;top:42px;width:135px;height:40px;font-size:21px;padding-top:3px}

/* hero */
.hero{position:absolute;left:0;top:126px;width:1200px;height:600px;
  background:linear-gradient(90deg,#8f8a86 0%,#a5705a 22%,#7a3a2a 45%,#4a1c16 62%,#1a0806 80%,#000 100%)}
.hero-copy{position:absolute;left:745px;top:205px;color:var(--white)}
.hero-welcome{font-size:29px;font-weight:300}
.hero-title{margin-top:10px;font-size:60px;font-weight:700;line-height:66px}
.hero-title .accent{color:var(--red)}
.btn--hero{position:absolute;left:746px;top:490px;width:144px;height:41px;font-size:21px;padding-top:3px}

/* services */
.section-title{position:absolute;left:0;width:1200px;text-align:center;font-weight:600;letter-spacing:1px}
.services-title{top:816px;font-size:36px}
.services-lead{position:absolute;top:870px;left:0;width:1200px;text-align:center;font-size:19px;font-weight:300;color:var(--muted)}
.card{position:absolute;width:317px}
.card-frame{width:317px;height:340px;background:var(--red);padding:12px}
.card-art{width:100%;height:100%}
.card-name{margin-top:20px;text-align:center;font-size:31px;font-weight:400;letter-spacing:1px}
.card-type{margin-top:4px;text-align:center;font-size:16px;font-weight:300;color:var(--red)}

/* newsletter */
.newsletter{position:absolute;left:0;top:2340px;width:1200px;height:351px;
  background:linear-gradient(90deg,#1d1612 0%,#3b2a1e 20%,#6b4a22 38%,#5a2418 55%,#3d2a1c 72%,#1a1714 100%)}
.newsletter-title{top:68px;font-size:32px;color:var(--white)}
.newsletter-text{position:absolute;top:130px;left:0;width:1200px;text-align:center;color:var(--white);font-size:19px;font-weight:300;line-height:32px}
.email-field{position:absolute;left:239px;top:220px;width:497px;height:60px;border:1.5px solid var(--white);border-radius:30px;color:var(--white);font-size:16px;font-weight:300;padding:20px 0 0 27px}
.btn-subscribe{position:absolute;left:762px;top:220px;width:198px;height:60px;border-radius:30px;background:var(--red);color:var(--white);font-size:25px;font-weight:600;display:flex;align-items:center;justify-content:center;padding-top:3px}

/* footer */
.brand--footer{left:111px;top:2855px;font-size:26px}
.footer-nav{position:absolute;top:2777px;right:115px;display:flex;gap:58px;font-size:20px;font-weight:400}
.footer-nav a{color:var(--ink);text-decoration:none}
.footer-rule{position:absolute;left:502px;top:2831px;width:586px;height:1.5px;background:var(--red)}
.copyright{position:absolute;top:2860px;right:113px;font-size:16px;font-weight:400}
</style>
</head>
<body>

<header class="site-header">
  <div class="brand brand--header"><span class="brand-mark"></span>QUIET HARBOR PRINTS</div>
  <nav class="main-nav">
    <a href="#">Künstler</a><a href="#">Veranstaltungen</a><a href="#">Shop</a><a href="#">About Us</a>
  </nav>
  <a class="btn btn--login" href="#">Login</a>
</header>

<section class="hero" role="img" aria-label="Smiling artist in a straw hat with arms crossed in a studio full of colourful paintings">
</section>
<div class="hero-copy">
  <div class="hero-welcome">Welcome To</div>
  <div class="hero-title"><span class="accent">QUIET</span><br>HARBOR<br><span class="accent">PRINTS</span></div>
</div>
<a class="btn btn--hero" href="#">Get Started</a>

<h2 class="section-title services-title">OUR SERVICES</h2>
<p class="services-lead">Lorem ipsum dolor sit amet, consectetur adipiscing</p>

<!-- row 1 -->
<div class="card" style="left:111px;top:924px">
  <div class="card-frame"><div class="card-art" role="img" aria-label="Abstract swirling paint in pink, blue and yellow" style="background:linear-gradient(135deg,#d23a6a,#2a8ac8 45%,#f0b030 70%,#6a2a7a)"></div></div>
  <div class="card-name">Accusantium</div><div class="card-type">Original artwork</div>
</div>
<div class="card" style="left:442px;top:924px">
  <div class="card-frame"><div class="card-art" role="img" aria-label="Colourful painted portrait of three people in profile" style="background:linear-gradient(135deg,#2a6a6a,#c8742a 50%,#3a2a20)"></div></div>
  <div class="card-name">Laudantium</div><div class="card-type">Original artwork</div>
</div>
<div class="card" style="left:771px;top:924px">
  <div class="card-frame"><div class="card-art" role="img" aria-label="Artist painting a large blue and orange canvas" style="background:linear-gradient(160deg,#3a78a8,#5a90b8 45%,#c8502a 75%,#2a3a4a)"></div></div>
  <div class="card-name">Voluptatem</div><div class="card-type">Original artwork</div>
</div>

<!-- row 2 -->
<div class="card" style="left:111px;top:1373px">
  <div class="card-frame"><div class="card-art" role="img" aria-label="Modern gallery hall with abstract paintings and sculpture" style="background:linear-gradient(135deg,#2e4a5a,#c86a3a 35%,#d8cfc4 65%,#4a5a64)"></div></div>
  <div class="card-name">Accusantium</div><div class="card-type">Original artwork</div>
</div>
<div class="card" style="left:442px;top:1373px">
  <div class="card-frame"><div class="card-art" role="img" aria-label="Classic museum room with skylight and landscape paintings" style="background:linear-gradient(180deg,#d8d8d4,#4a4e52 35%,#8a7a62 65%,#c89a5a)"></div></div>
  <div class="card-name">Laudantium</div><div class="card-type">Original artwork</div>
</div>
<div class="card" style="left:771px;top:1373px">
  <div class="card-frame"><div class="card-art" role="img" aria-label="Studio wall with a large abstract canvas above a worktable" style="background:linear-gradient(160deg,#6a4a3a,#c88a3a 40%,#3a6a7a 70%,#2a2420)"></div></div>
  <div class="card-name">Voluptatem</div><div class="card-type">Original artwork</div>
</div>

<!-- row 3 -->
<div class="card" style="left:111px;top:1821px">
  <div class="card-frame"><div class="card-art" role="img" aria-label="Women painting together at a workshop table" style="background:linear-gradient(135deg,#c8b8a8,#8a5a3a 45%,#e8e0d8 75%,#2a2220)"></div></div>
  <div class="card-name">Accusantium</div><div class="card-type">Original artwork</div>
</div>
<div class="card" style="left:442px;top:1821px">
  <div class="card-frame"><div class="card-art" role="img" aria-label="Artist drawing at a bright white desk" style="background:linear-gradient(160deg,#eeeeec,#dcdad6 50%,#a07a4a 80%,#3a3a3a)"></div></div>
  <div class="card-name">Laudantium</div><div class="card-type">Original artwork</div>
</div>
<div class="card" style="left:771px;top:1821px">
  <div class="card-frame"><div class="card-art" role="img" aria-label="Graphic collage painting with flowers in teal, pink and yellow" style="background:linear-gradient(135deg,#3ab0b0,#e88aa0 40%,#f0c040 65%,#2a3a6a)"></div></div>
  <div class="card-name">Voluptatem</div><div class="card-type">Original artwork</div>
</div>

<section class="newsletter" role="img" aria-label="Dark streaked paint texture background">
  <h2 class="section-title newsletter-title">SUBSCRIBE TO OUR NEWSLETTER</h2>
  <p class="newsletter-text">Lorem ipsum dolor sit amet, consectetur adipiscing elit, sed do eiusmod tempor<br>incididunt ut labore et dolore magna aliqua.</p>
  <div class="email-field">Email Address</div>
  <div class="btn-subscribe">Subscribe</div>
</section>

<footer>
  <div class="brand brand--footer"><span class="brand-mark"></span>QUIET HARBOR PRINTS</div>
  <nav class="footer-nav">
    <a href="#">Künstler</a><a href="#">Veranstaltungen</a><a href="#">Shop</a><a href="#">About Us</a>
  </nav>
  <div class="footer-rule"></div>
  <p class="copyright">© copyrights 2024 Quiet Harbor Prints. &nbsp;| &nbsp;All Rights Reserved</p>
</footer>

</body>
</html>
```